New Innovative Counselling and psychotherapy Service needs Business Card design

Keep it simple and professional. On one side, just company name and logo (perhaps in all blue) and maybe a tag line.

On other side (all white) my name and Qualifications in centre

Industry/Entity Type

Health And Wellness

Contact Information for Business Card

Dara Whelby
Counsellor & Psychotherapist
BSc (Psychol.), BA, Dip. (Couns. & Psych.), PG.Cert (CBT), FGTrK, ONRE

I will also require Mobile no, Email and web site address of which I'll pass on to final designer.

Font styles to use
Sans Serif

Requirements
Must have
• My Logo Only and please use the colours in logo that is in it.
Should not have
• Any other images

```html
<!DOCTYPE html>
<html lang="en">
<head>
<meta charset="utf-8">
<title>Thrivelane Business Card</title>
<link href="https://fonts.googleapis.com/css2?family=Work+Sans:wght@300;400;500&display=swap" rel="stylesheet">
<style>
  :root {
    --stage: #161616;
    --card-dark: #2c2c2c;
    --card-white: #ffffff;
    --brand-blue: #44a3da;
    --brand-green: #7cb342;
    --ink-light: #e6e6e6;
    --ink-dark: #2b2b2b;
  }
  * { margin: 0; padding: 0; box-sizing: border-box; }
  html, body {
    width: 1200px; height: 963px; overflow: hidden;
    background: var(--stage);
    font-family: "Work Sans", Arial, sans-serif;
  }
  .canvas {
    width: 1200px; height: 963px;
    display: flex; flex-direction: column; align-items: center; justify-content: center;
    gap: 56px;
  }
  .card {
    position: relative;
    width: 700px; height: 400px;
    border-radius: 22px;
    overflow: hidden;
    background: var(--card-dark);
    box-shadow: 0 18px 40px rgba(0,0,0,.55);
  }
  .card-front__shape { position: absolute; inset: 0; }
  .contact-block {
    position: absolute; left: 44px; top: 74px; width: 300px;
    color: var(--ink-light);
  }
  .holder-name {
    font-size: 31px; font-weight: 500; letter-spacing: .5px;
    color: var(--brand-blue); text-transform: uppercase;
    line-height: 1.1; margin-bottom: 10px;
  }
  .holder-role { font-size: 15px; font-weight: 400; margin-bottom: 4px; }
  .holder-quals { font-size: 14px; font-weight: 300; line-height: 1.45; margin-bottom: 22px; }
  .contact-list { list-style: none; font-size: 15px; font-weight: 300; line-height: 1.8; }
  .contact-list li { display: flex; align-items: center; gap: 10px; }
  .contact-list svg { width: 14px; height: 14px; flex: none; }
  .brand-front {
    position: absolute; left: 450px; top: 100px;
    display: flex; align-items: center; gap: 12px;
  }
  .brand-dot { width: 26px; height: 26px; border-radius: 50%; background: var(--brand-blue); }
  .brand-front .brand-name {
    font-size: 38px; font-weight: 300; color: var(--ink-dark); letter-spacing: .5px;
  }
  .card-back { display: flex; flex-direction: column; align-items: center; justify-content: center; gap: 34px; }
  .brand-back { display: flex; align-items: center; gap: 18px; }
  .brand-back .brand-dot { width: 44px; height: 44px; }
  .brand-back .brand-name { font-size: 60px; font-weight: 300; color: var(--brand-blue); }
  .web-address { font-size: 19px; font-weight: 400; color: var(--ink-light); letter-spacing: .5px; }
  .web-address .accent { color: var(--brand-green); }
</style>
</head>
<body>
<main class="canvas">
  <section class="card card-front" aria-label="Business card front">
    <svg class="card-front__shape" viewBox="0 0 700 400" preserveAspectRatio="none" aria-hidden="true">
      <path d="M700 0 L405 0 C330 70 330 230 505 400 L700 400 Z" fill="var(--card-white)"/>
      <path d="M395 0 C318 72 318 232 492 400" fill="none" stroke="var(--brand-blue)" stroke-width="9"/>
    </svg>
    <div class="contact-block">
      <h1 class="holder-name">Dara Whelby</h1>
      <p class="holder-role">Counsellor &amp; Psychotherapist</p>
      <p class="holder-quals">BSc (Psychol.), BA, Dip.<br>(Couns. &amp; Psych.), PG.Cert<br>(CBT), FGTrK, ONRE</p>
      <ul class="contact-list">
        <li><svg viewBox="0 0 24 24"><path fill="#e6e6e6" d="M6.6 10.8a15 15 0 0 0 6.6 6.6l2.2-2.2a1 1 0 0 1 1-.25 11.4 11.4 0 0 0 3.6.57 1 1 0 0 1 1 1V20a1 1 0 0 1-1 1A17 17 0 0 1 3 4a1 1 0 0 1 1-1h3.5a1 1 0 0 1 1 1c0 1.25.2 2.45.57 3.6a1 1 0 0 1-.25 1z"/></svg>888-555-0142</li>
        <li><svg viewBox="0 0 24 24"><rect x="3" y="5" width="18" height="14" rx="2" fill="none" stroke="#e6e6e6" stroke-width="2"/><path d="M3 6l9 7 9-7" fill="none" stroke="#e6e6e6" stroke-width="2"/></svg>info@thrivelane.com</li>
        <li><svg viewBox="0 0 24 24"><circle cx="12" cy="12" r="9" fill="none" stroke="#e6e6e6" stroke-width="2"/><path d="M3 12h18M12 3c3 3 3 15 0 18M12 3c-3 3-3 15 0 18" fill="none" stroke="#e6e6e6" stroke-width="1.5"/></svg>www.thrivelane.com</li>
      </ul>
    </div>
    <div class="brand-front">
      <span class="brand-dot"></span>
      <span class="brand-name">Thrivelane</span>
    </div>
  </section>

  <section class="card card-back" aria-label="Business card back">
    <div class="brand-back">
      <span class="brand-dot"></span>
      <span class="brand-name">Thrivelane</span>
    </div>
    <p class="web-address">www.<span class="accent">thrivelane</span>.com</p>
  </section>
</main>
</body>
</html>
```